Carwash Signage

We own and operate a 25m tunnel car wash in the uk. We are looking to upgrade our signage to include the following:-

Wash selection Board Size-1300x1300mm
Conditions 1300x1300mm
Instructions 1300x1300mm
Banner 2600x600mm
Stamp card flyer a5 double sided - 9 squares for stamping 3rd square needs to say free air freshener 9th square needs to say free vip car wash.

I have attached some notes for the details that are required to be included.

We are looking for a modern smart look more European car wash style than American car wash style. It should be bold and clear. with yellow/orange & blue/green,grey colours

The final design must be in a industry standard printable format.

UPDATED BRIEF AS DISCUSSED: We require design for 2 x window decals, flag design and 50% off voucher. Attached are rough layout drawings of what they should look like - we expect the designs to be in keeping with the previous designs colours, etc that have been carried out. We Look forward to hearing from you.

Target Market(s)

local car owners within a 15-20 mile radius

Colors
0054AA
0677BA
7BADD7
CADEEF
E8F1F8
0094D4
00A9DD
6FCCEA
C7EBF8
E9F6FB
00AB8E
00BBA5
67D7C9
C6EFE9
E9F9F6

Requirements
Must have
• must be sharp and modern European look

```html
<!DOCTYPE html>
<html lang="en">
<head>
<meta charset="utf-8">
<title>Instructions Board – Harbourside Car Wash</title>
<link href="https://fonts.googleapis.com/css2?family=Poppins:wght@500;600;700&display=swap" rel="stylesheet">
<style>
  :root {
    --backdrop: #8a8a8a;
    --board-top: #1c7099;
    --board-bottom: #1f3a54;
    --heading-orange: #f6b325;
    --closing-yellow: #f3ec1b;
    --text-white: #ffffff;
    --brand-blue: #0054aa;
    --brand-panel: #ffffff;
  }
  * { margin: 0; padding: 0; box-sizing: border-box; }
  html, body {
    width: 1200px;
    height: 1000px;
    overflow: hidden;
    background: var(--backdrop);
  }
  .canvas {
    position: relative;
    width: 1200px;
    height: 1000px;
    font-family: "Poppins", sans-serif;
  }
  .board {
    position: absolute;
    left: 197px;
    top: 97px;
    width: 806px;
    height: 806px;
    background: linear-gradient(180deg, var(--board-top) 0%, var(--board-bottom) 100%);
  }
  .brand-panel {
    position: absolute;
    left: 15px;
    top: 15px;
    width: 196px;
    height: 68px;
    background: var(--brand-panel);
    display: flex;
    align-items: center;
    justify-content: center;
    gap: 8px;
  }
  .brand-dot {
    width: 14px;
    height: 14px;
    border-radius: 50%;
    background: var(--brand-blue);
    flex: none;
  }
  .brand-name {
    font-weight: 700;
    font-size: 15px;
    line-height: 1.1;
    color: var(--brand-blue);
    text-transform: uppercase;
  }
  .board-title {
    position: absolute;
    left: 0;
    width: 806px;
    top: 62px;
    text-align: center;
    font-weight: 700;
    font-size: 31px;
    color: var(--heading-orange);
    letter-spacing: 0.5px;
  }
  .board-subtitle {
    position: absolute;
    left: 88px;
    top: 106px;
    font-weight: 700;
    font-size: 20px;
    color: var(--heading-orange);
  }
  .steps {
    position: absolute;
    left: 88px;
    top: 150px;
    list-style: none;
    color: var(--text-white);
    font-weight: 600;
    font-size: 20.5px;
    line-height: 32.7px;
  }
  .steps .sub { padding-left: 28px; }
  .closing {
    position: absolute;
    left: 0;
    width: 806px;
    top: 710px;
    text-align: center;
    font-weight: 700;
    font-size: 41px;
    color: var(--closing-yellow);
  }
  .closing-rule {
    position: absolute;
    left: 86px;
    top: 771px;
    width: 630px;
    height: 2px;
    background: var(--text-white);
  }
</style>
</head>
<body>
<div class="canvas">
  <section class="board">
    <div class="brand-panel">
      <span class="brand-dot"></span>
      <span class="brand-name">Harbourside Car Wash</span>
    </div>
    <h1 class="board-title">INSTRUCTIONS</h1>
    <p class="board-subtitle">CHECK FOR LOOSE ITEMS BEFORE ENTERING THE WASH</p>
    <ul class="steps">
      <li>* LOWER AERIAL - if electrical make sure</li>
      <li>the aerial is fully retracted, operator may</li>
      <li>assist but is not responsible for the condition of</li>
      <li>your car.</li>
      <li>* DRIVE FORWARD UNTIL OPERATOR TELLS YOU TO STOP</li>
      <li>* OPERATOR WILL GUIDE YOU INTO THE CARWASH</li>
      <li>* ONCE ON CONVEYOR TRACK</li>
      <li class="sub">- HAND BRAKE OFF</li>
      <li class="sub">- SELECT NEUTRAL GEAR</li>
      <li class="sub">- CLOSE ALL WINDOWS + SUNROOF</li>
      <li class="sub">- LEAVE ENGINE RUNNING</li>
      <li class="sub">- TURN AUTO WIPERS OFF</li>
      <li>* DO NOT BRAKE</li>
      <li>* DO NOT STEER</li>
      <li>* DO NOT ATTEMPT EXIT VEHICLE</li>
      <li>* AT END OF WASH. DRIVE AWAY WHEN TRAFFIC LIGHT</li>
      <li>* GREEN TURNS</li>
    </ul>
    <p class="closing">ENJOY THE RIDE</p>
    <div class="closing-rule"></div>
  </section>
</div>
</body>
</html>
```